One Page Website for Personal Trainer in London

I have a logo and need a one page website designed around my branding. I am a freelance Personal Trainer based in London specialising in bodyweight training for men and women. I would like the site to be modern and clean but not overtly urban in design.
I need the following headings:
About Me
My Services
Events
Blog
I don't need them to be seperate pages but if they can link to further down the page that would be great.
Industry/Entity Type
Personal Trainer
Coding
Coded - Design and coding required
Number of Pages Required
1 page
Requirements
Must have
- I need the following headings:
- About Me
- My Services
- Events
- Blog
- mobile friendly formatting
- health and fitness related photography
- Colour scheme in keeping with my existing logo

```html
<!DOCTYPE html>
<html lang="en">
<head>
<meta charset="utf-8">
<title>Harlow Reeve Personal Training</title>
<link href="https://fonts.googleapis.com/css2?family=Open+Sans:ital,wght@0,400;0,600;0,700;0,800;1,400;1,600&family=Montserrat:wght@500;600;700&family=Lora:wght@400&display=swap" rel="stylesheet">
<style>
:root{
  --orange:#f7941d;
  --orange-dark:#e2820f;
  --ink:#222222;
  --charcoal:#2b2b2b;
  --grey-text:#8a8a8a;
  --light:#f2f2f2;
  --white:#ffffff;
}
*{margin:0;padding:0;box-sizing:border-box}
html,body{width:1200px;height:4091px;overflow:hidden}
body{font-family:"Open Sans",Arial,sans-serif;color:var(--ink);background:var(--white);position:relative}
section,header,nav,footer{position:absolute;left:0;width:1200px}
.abs{position:absolute}
.photo{position:absolute}

/* top */
.topline{top:0;height:10px;background:var(--charcoal)}
.site-header{top:10px;height:132px}
.brand{left:130px;top:22px;width:180px;text-align:center}
.brand-mark{width:34px;height:34px;background:var(--orange);border-radius:50%;margin:0 auto 8px}
.brand-name{font-family:"Montserrat",sans-serif;font-weight:600;font-size:20px;color:var(--ink);line-height:1}
.brand-tag{font-family:"Montserrat",sans-serif;font-weight:600;font-size:9px;letter-spacing:2px;color:var(--ink);margin-top:5px}
.contact-bar{right:130px;top:58px;display:flex;gap:38px;font-family:"Montserrat",sans-serif;font-weight:600;font-size:19px}
.contact-bar span{display:flex;align-items:center;gap:10px}
.contact-bar svg{width:26px;height:26px}

.main-nav{top:142px;height:38px;background:var(--orange)}
.main-nav ul{list-style:none;display:flex;position:absolute;left:136px;top:0;height:38px}
.main-nav li{width:125px;text-align:center;line-height:38px;font-family:"Montserrat",sans-serif;font-weight:600;font-size:12px;color:var(--ink);border-right:1px solid rgba(0,0,0,.15)}
.main-nav li.active{background:var(--orange-dark);width:100px;color:var(--white)}
.nav-cta{position:absolute;left:867px;top:0;width:205px;height:38px;background:var(--charcoal);color:var(--white);font-family:"Montserrat",sans-serif;font-weight:600;font-size:12px;line-height:38px;text-align:center}

/* hero */
.hero{top:180px;height:682px;overflow:hidden}
.hero .photo{inset:0;background:
  linear-gradient(180deg,rgba(0,0,0,.15) 0%,rgba(0,0,0,.05) 40%,rgba(0,0,0,.55) 100%),
  radial-gradient(ellipse 260px 320px at 870px 300px,#3f78a8 0%,rgba(63,120,168,0) 70%),
  radial-gradient(ellipse 200px 220px at 470px 330px,#b98c74 0%,rgba(185,140,116,0) 70%),
  radial-gradient(ellipse 380px 200px at 200px 90px,#c9c6c0 0%,rgba(201,198,192,0) 75%),
  radial-gradient(ellipse 300px 180px at 1080px 120px,#a9a6a0 0%,rgba(169,166,160,0) 75%),
  linear-gradient(90deg,#2a2b2d 0%,#55565a 30%,#4a4b4e 65%,#2c2d30 100%)}
.hero-text{position:absolute;left:0;width:1200px;top:355px;text-align:center;color:var(--white)}
.hero-kicker{font-style:italic;font-size:46px;font-weight:400;line-height:1}
.hero-title{font-weight:800;font-size:66px;color:var(--orange);letter-spacing:1px;line-height:1;margin-top:14px}
.hero-sub{font-size:26px;margin-top:18px}
.btn{display:inline-block;background:var(--orange);color:var(--white);font-family:"Montserrat",sans-serif;font-weight:500}
.hero .btn{position:absolute;left:473px;top:572px;width:230px;height:53px;line-height:53px;font-size:18px;text-align:center}

/* about */
.about{top:862px;height:488px}
.about .photo{left:560px;top:0;width:640px;height:488px;background:
  radial-gradient(ellipse 130px 150px at 340px 150px,#caa28c 0%,rgba(202,162,140,0) 75%),
  radial-gradient(ellipse 90px 70px at 170px 190px,#7fc1d6 0%,rgba(127,193,214,0) 75%),
  radial-gradient(ellipse 260px 170px at 330px 420px,#3c6e9b 0%,rgba(60,110,155,0) 75%),
  radial-gradient(ellipse 110px 110px at 430px 80px,#3a2d29 0%,rgba(58,45,41,0) 75%),
  linear-gradient(90deg,#ffffff 0%,#f1f1f1 25%,#e4e4e4 60%,#cfcfcf 100%)}
.section-title{font-family:"Montserrat",sans-serif;font-weight:700;font-size:44px;color:var(--ink)}
.about .section-title{position:absolute;left:150px;top:86px}
.about-lead{position:absolute;left:144px;top:185px;width:420px;font-size:14.5px;font-weight:600;line-height:1.3;text-transform:uppercase}
.about-body{position:absolute;left:144px;top:258px;width:420px;font-size:12.5px;line-height:1.6;color:var(--grey-text)}
.btn-square{position:absolute;display:flex;height:32px;font-family:"Montserrat",sans-serif;font-weight:600;font-size:11px;color:var(--white)}
.btn-square .label{background:var(--orange);padding:0 20px;line-height:32px}
.btn-square .tip{width:32px;background:var(--charcoal)}
.about .btn-square{left:142px;top:392px}

/* banner */
.banner{top:1350px;height:477px;overflow:hidden}
.banner .photo{inset:0;background:
  linear-gradient(180deg,rgba(0,0,0,.35) 0%,rgba(0,0,0,.15) 45%,rgba(0,0,0,.4) 100%),
  radial-gradient(ellipse 240px 300px at 1040px 250px,#cfd2d4 0%,rgba(207,210,212,0) 75%),
  radial-gradient(ellipse 200px 260px at 150px 230px,#9a9896 0%,rgba(154,152,150,0) 75%),
  radial-gradient(ellipse 170px 140px at 560px 90px,#8a7365 0%,rgba(138,115,101,0) 75%),
  radial-gradient(ellipse 300px 120px at 600px 430px,#2d2d2e 0%,rgba(45,45,46,0) 80%),
  linear-gradient(90deg,#4f4e4d 0%,#6f6d6b 45%,#5e5d5c 75%,#8c8d8f 100%)}
.banner-text{position:absolute;left:0;width:1200px;top:152px;text-align:center;color:var(--white)}
.banner-kicker{font-style:italic;font-weight:600;font-size:23px}
.banner-title{font-weight:600;font-size:56px;line-height:1.05;margin-top:14px}

/* services */
.services{top:1827px;height:758px}
.services .section-title{position:absolute;width:1200px;text-align:center;top:64px}
.service{position:absolute;top:150px;text-align:center}
.service .photo{position:relative;height:330px;border-radius:0 140px 140px 140px}
.service h3{color:var(--orange);font-size:16px;font-weight:700;margin-top:38px}
.service p{font-size:12px;line-height:1.4;color:var(--ink);margin-top:8px}
.svc-1{left:100px;width:255px}
.svc-1 .photo{background:
  radial-gradient(ellipse 60px 120px at 125px 200px,#3f4a57 0%,rgba(63,74,87,0) 80%),
  linear-gradient(180deg,#b9d4e6 0%,#93b6cf 45%,#5c7f9b 62%,#8a8f93 78%,#6b6f73 100%)}
.svc-2{left:423px;width:307px}
.svc-2 .photo{background:
  radial-gradient(ellipse 120px 80px at 150px 170px,#c2483d 0%,rgba(194,72,61,0) 80%),
  radial-gradient(ellipse 80px 70px at 150px 120px,#a87a63 0%,rgba(168,122,99,0) 80%),
  linear-gradient(180deg,#2f2e2d 0%,#4a423e 55%,#8a8784 80%,#5f5d5b 100%)}
.svc-3{left:766px;width:286px}
.svc-3 .photo{background:
  radial-gradient(ellipse 90px 70px at 100px 110px,#e6c993 0%,rgba(230,201,147,0) 80%),
  radial-gradient(ellipse 130px 80px at 150px 210px,#4d6d86 0%,rgba(77,109,134,0) 80%),
  linear-gradient(180deg,#e2e0dc 0%,#b9b3ab 50%,#8a827a 100%)}
.services .btn-square{left:524px;top:646px}

/* blog */
.blog{top:2585px;height:764px;background:var(--orange)}
.blog .section-title{position:absolute;width:1200px;text-align:center;top:60px;color:var(--white)}
.post{position:absolute;top:188px;width:267px;height:327px;background:var(--white);border-radius:6px;overflow:hidden;box-shadow:0 4px 10px rgba(0,0,0,.12)}
.post .photo{position:relative;height:187px}
.post-date{position:absolute;left:8px;top:10px;width:46px;height:46px;background:var(--orange);color:var(--white);text-align:center;font-weight:700;font-size:22px;line-height:1.2;padding-top:2px}
.post-date small{display:block;font-size:7px;font-weight:600}
.post h4{font-size:15px;font-weight:700;line-height:1.3;padding:16px 20px 0}
.post p{font-size:11px;line-height:1.4;color:var(--grey-text);padding:8px 20px 0}
.post-1{left:41px}.post-1 .photo{background:
  radial-gradient(ellipse 90px 60px at 200px 120px,#e8617c 0%,rgba(232,97,124,0) 80%),
  radial-gradient(ellipse 80px 70px at 120px 80px,#c9957a 0%,rgba(201,149,122,0) 80%),
  linear-gradient(135deg,#dbe4ea 0%,#aab9c3 60%,#8395a1 100%)}
.post-2{left:325px}.post-2 .photo{background:
  radial-gradient(ellipse 60px 90px at 100px 100px,#6f6a66 0%,rgba(111,106,102,0) 80%),
  radial-gradient(ellipse 70px 90px at 200px 90px,#c48b5a 0%,rgba(196,139,90,0) 80%),
  linear-gradient(135deg,#f0e3c8 0%,#d4b98e 55%,#9c8466 100%)}
.post-3{left:608px}.post-3 .photo{background:
  radial-gradient(ellipse 70px 80px at 150px 80px,#d8ab94 0%,rgba(216,171,148,0) 80%),
  radial-gradient(ellipse 80px 50px at 80px 150px,#2fa9c9 0%,rgba(47,169,201,0) 80%),
  radial-gradient(ellipse 60px 40px at 60px 90px,#c04b8c 0%,rgba(192,75,140,0) 80%),
  linear-gradient(135deg,#e9f0f2 0%,#c2d4da 60%,#9db8c2 100%)}
.post-4{left:892px}.post-4 .photo{background:
  radial-gradient(ellipse 120px 60px at 130px 160px,#5a3a3a 0%,rgba(90,58,58,0) 80%),
  radial-gradient(ellipse 160px 90px at 200px 30px,#fff0b8 0%,rgba(255,240,184,0) 80%),
  linear-gradient(160deg,#ffc86b 0%,#f29a3a 50%,#9c5a2c 100%)}
.blog .btn-square{left:503px;top:605px}
.blog .btn-square .label{background:var(--white);color:var(--orange)}

/* events & testimonials */
.lower{top:3349px;height:387px}
.col-title{position:absolute;font-family:"Montserrat",sans-serif;font-weight:600;font-size:27px;color:var(--orange)}
.arrows{position:absolute;display:flex;gap:6px}
.arrows svg{width:20px;height:20px}
.rule{position:absolute;height:1px;background:#dddddd}
.event{position:absolute;left:100px;width:460px}
.event-date{position:absolute;left:0;top:0;width:50px;text-align:center;font-weight:700}
.event-date .day{background:var(--charcoal);color:var(--white);font-size:20px;height:40px;line-height:40px}
.event-date .month{background:var(--orange);color:var(--white);font-size:13px;height:26px;line-height:26px;font-weight:600}
.event h5{position:absolute;left:91px;top:-2px;font-size:15px;font-weight:700}
.event p{position:absolute;left:91px;top:28px;width:370px;font-size:12px;line-height:1.5;color:var(--grey-text)}
.avatar{position:absolute;left:668px;top:92px;width:138px;height:138px;border-radius:50%;background:
  radial-gradient(ellipse 40px 50px at 69px 60px,#d9a98f 0%,rgba(217,169,143,0) 80%),
  radial-gradient(ellipse 60px 30px at 69px 130px,#d94a5a 0%,rgba(217,74,90,0) 80%),
  linear-gradient(160deg,#f2f2f2,#d8d2ce)}
.avatar-name{position:absolute;left:668px;top:240px;width:138px;text-align:center;color:var(--orange);font-weight:700;font-size:12px}
.quote{position:absolute;left:826px;top:92px;width:300px;font-size:12px;line-height:1.5;color:var(--grey-text)}
.quote b{color:var(--orange);font-size:18px}

/* footer */
.site-footer{top:3736px;height:327px;background:var(--charcoal);color:var(--white)}
.footer-curve{position:absolute;left:-100px;top:-40px;width:1400px;height:90px;background:var(--white);border-radius:0 0 50% 50%}
.foot-brand{position:absolute;left:88px;top:100px;width:220px;text-align:center}
.foot-brand .brand-name,.foot-brand .brand-tag{color:var(--white)}
.foot-about{position:absolute;left:88px;top:185px;width:250px;font-size:11.5px;line-height:1.45;color:#cfcfcf}
.vline{position:absolute;top:80px;width:1px;height:210px;background:#555555}
.foot-head{position:absolute;font-family:"Montserrat",sans-serif;font-weight:600;font-size:15px;color:var(--orange)}
.foot-links{position:absolute;left:431px;top:134px;list-style:none;font-size:13px;line-height:26.5px}
.foot-links li::before{content:"\2022";margin-right:8px;color:var(--orange)}
.foot-contact{position:absolute;left:654px;top:134px;font-size:12px;line-height:1.5}
.foot-contact .row{display:flex;align-items:center;gap:7px;margin-top:6px}
.foot-contact svg{width:12px;height:12px;flex:none}
.social{position:absolute;left:924px;top:136px;display:flex;gap:14px}
.social span{width:14px;height:14px;border-radius:50%;background:var(--white)}
.call-label{position:absolute;left:924px;top:190px;font-family:"Montserrat",sans-serif;font-weight:600;font-size:15px}
.call-number{position:absolute;left:924px;top:212px;font-family:"Lora",serif;font-size:27px}
.foot-strip{position:absolute;left:0;top:4063px;width:1200px;height:28px;background:var(--orange-dark);text-align:center;font-size:9px;line-height:28px;color:var(--charcoal)}
</style>
</head>
<body>

<div class="abs topline" style="left:0;width:1200px"></div>

<header class="site-header">
  <div class="abs brand">
    <div class="brand-mark"></div>
    <div class="brand-name">Harlow Reeve</div>
    <div class="brand-tag">PERSONAL TRAINING</div>
  </div>
  <div class="abs contact-bar">
    <span><svg viewBox="0 0 26 26"><circle cx="13" cy="13" r="12" fill="none" stroke="#f7941d" stroke-width="2"/><path d="M9 8c1-1 2 0 3 2s-1 2 0 3 2 2 3 1 2 0 3 1-1 3-3 3-8-5-7-9z" fill="#f7941d"/></svg>(555) 274 0913</span>
    <span><svg viewBox="0 0 26 26"><circle cx="13" cy="13" r="12" fill="none" stroke="#f7941d" stroke-width="2"/><rect x="7" y="9" width="12" height="8" fill="#f7941d"/><path d="M7 9l6 5 6-5" stroke="#fff" fill="none"/></svg>hello@harlowreeve.co</span>
  </div>
</header>

<nav class="main-nav">
  <ul>
    <li class="active">HOME</li>
    <li>ABOUT ME</li>
    <li>MY SERVICES</li>
    <li>EVENTS</li>
    <li>BLOG</li>
    <li>CONTACT US</li>
  </ul>
  <a class="nav-cta">START TRAINING NOW</a>
</nav>

<section class="hero">
  <div class="photo" role="img" aria-label="Trainer coaching a woman through suspension strap training in a gym"></div>
  <div class="hero-text">
    <div class="hero-kicker">Start adding</div>
    <div class="hero-title">BODY WEIGHT MOVEMENTS</div>
    <div class="hero-sub">into your training &amp; enjoy the results!</div>
  </div>
  <a class="btn">Start training Now</a>
</section>

<section class="about" id="about">
  <div class="photo" role="img" aria-label="Woman in sportswear drinking from a water bottle after a workout"></div>
  <h2 class="section-title">About us</h2>
  <p class="about-lead">Negare non possum. Dolore malum est: in crucem qui agitur, beatus esse non potest. Quae cum dixisset paulumque institisset</p>
  <p class="about-body">Training should fit your life, not the other way round. I build simple routines that use your own bodyweight, so you can train at home, in the park or on the road. Every plan is shaped around your goals, your schedule and the way you like to move, with steady progress.</p>
  <a class="btn-square"><span class="label">READ MORE</span><span class="tip"></span></a>
</section>

<section class="banner">
  <div class="photo" role="img" aria-label="Group of people doing squat exercises in a bright studio"></div>
  <div class="banner-text">
    <div class="banner-kicker">I am a freelance Personal Trainer based in London specialising in</div>
    <div class="banner-title">Bodyweight training for<br>men and women.</div>
  </div>
</section>

<section class="services" id="services">
  <h2 class="section-title">Our Service</h2>
  <div class="service svc-1">
    <div class="photo" role="img" aria-label="Woman stretching in a lunge by the sea"></div>
    <h3>Stretching</h3>
    <p>Gentle mobility work to loosen tight muscles and keep joints moving well.</p>
  </div>
  <div class="service svc-2">
    <div class="photo" role="img" aria-label="Man doing a push-up on the gym floor"></div>
    <h3>Bodyweight Exercise</h3>
    <p>Push, pull and squat patterns that build real strength with no kit at all.</p>
  </div>
  <div class="service svc-3">
    <div class="photo" role="img" aria-label="Trainer guiding a client through a plank"></div>
    <h3>Fitness Plans</h3>
    <p>Weekly plans written for your goals and checked as you progress.</p>
  </div>
  <a class="btn-square"><span class="label">MORE SERVICE</span><span class="tip"></span></a>
</section>

<section class="blog" id="blog">
  <h2 class="section-title">Latest Blog</h2>
  <article class="post post-1">
    <div class="photo" role="img" aria-label="Woman resting after a run"><div class="post-date">22<small>October</small></div></div>
    <h4>Negare non possum. Dolore malum est</h4>
    <p>Five easy warm-up moves to do before any session, even short ones.</p>
  </article>
  <article class="post post-2">
    <div class="photo" role="img" aria-label="Runners on an outdoor track"><div class="post-date">23<small>October</small></div></div>
    <h4>Quod autem satis est, eo quic uid accessit</h4>
    <p>How to keep your training going when the weather turns cold and dark.</p>
  </article>
  <article class="post post-3">
    <div class="photo" role="img" aria-label="Smiling woman holding light dumbbells"><div class="post-date">24<small>October</small></div></div>
    <h4>Alios in primisque familiarem nostrum Posidonium</h4>
    <p>Why rest days matter as much as the hard work you put in each week.</p>
  </article>
  <article class="post post-4">
    <div class="photo" role="img" aria-label="Running shoes on a path at sunset"><div class="post-date">25<small>October</small></div></div>
    <h4>Vicimus. Hanc ergo intuens debet institutum</h4>
    <p>A simple guide to eating well around your workouts without fuss.</p>
  </article>
  <a class="btn-square"><span class="label">VIEW ALL BLOG POSTS</span><span class="tip"></span></a>
</section>

<section class="lower" id="events">
  <h2 class="col-title" style="left:95px;top:18px">Events</h2>
  <div class="arrows" style="left:514px;top:28px">
    <svg viewBox="0 0 20 20"><circle cx="10" cy="10" r="10" fill="#f7941d"/><path d="M12 5l-5 5 5 5" stroke="#fff" stroke-width="2" fill="none"/></svg>
    <svg viewBox="0 0 20 20"><circle cx="10" cy="10" r="10" fill="#f7941d"/><path d="M8 5l5 5-5 5" stroke="#fff" stroke-width="2" fill="none"/></svg>
  </div>
  <div class="rule" style="left:95px;top:68px;width:465px"></div>
  <div class="event" style="top:103px">
    <div class="event-date"><div class="day">30</div><div class="month">Oct</div></div>
    <h5>Verum tamen cum de rebus</h5>
    <p>Outdoor bootcamp in the park, all levels welcome, bring water and a mat.</p>
  </div>
  <div class="rule" style="left:95px;top:185px;width:465px"></div>
  <div class="event" style="top:201px">
    <div class="event-date"><div class="day">31</div><div class="month">Oct</div></div>
    <h5>Verum tamen cum de rebus</h5>
    <p>Evening core class for beginners, small group with plenty of coaching.</p>
  </div>

  <h2 class="col-title" style="left:660px;top:18px">Testimonials</h2>
  <div class="arrows" style="left:1078px;top:28px">
    <svg viewBox="0 0 20 20"><circle cx="10" cy="10" r="10" fill="#f7941d"/><path d="M12 5l-5 5 5 5" stroke="#fff" stroke-width="2" fill="none"/></svg>
    <svg viewBox="0 0 20 20"><circle cx="10" cy="10" r="10" fill="#f7941d"/><path d="M8 5l5 5-5 5" stroke="#fff" stroke-width="2" fill="none"/></svg>
  </div>
  <div class="rule" style="left:660px;top:68px;width:465px"></div>
  <div class="avatar" role="img" aria-label="Portrait of a happy client"></div>
  <div class="avatar-name">MAYA</div>
  <p class="quote"><b>&ldquo;</b> I had never trained without machines before. Within two months I felt stronger, slept better and actually looked forward to each session. The plans are clear, the coaching is patient and every workout fits into my busy week. I could not recommend it more to anyone starting out. <b>&rdquo;</b></p>
</section>

<footer class="site-footer">
  <div class="footer-curve"></div>
  <div class="foot-brand">
    <div class="brand-mark"></div>
    <div class="brand-name">Harlow Reeve</div>
    <div class="brand-tag">PERSONAL TRAINING</div>
  </div>
  <p class="foot-about">Bodyweight coaching for men and women across London. Simple plans, real progress and training you can do anywhere, at any level.</p>
  <div class="vline" style="left:376px"></div>
  <div class="vline" style="left:627px"></div>
  <div class="vline" style="left:900px"></div>

  <div class="foot-head" style="left:431px;top:100px">QUICK LINKS</div>
  <ul class="foot-links">
    <li>Home</li><li>About Us</li><li>services</li><li>Events</li><li>Blogs</li><li>Contact</li>
  </ul>

  <div class="foot-head" style="left:654px;top:100px">CONTACT</div>
  <div class="foot-contact">
    <div>42 Linden Row<br>Camberwell, SE5 7QT</div>
    <div class="row"><svg viewBox="0 0 12 12"><path d="M2 1c1-1 2 0 3 2s-1 2 0 3 2 2 3 1 2 0 3 1-1 3-3 3-7-5-6-10z" fill="#fff"/></svg>555-410-2286</div>
    <div class="row"><svg viewBox="0 0 12 12"><path d="M2 1c1-1 2 0 3 2s-1 2 0 3 2 2 3 1 2 0 3 1-1 3-3 3-7-5-6-10z" fill="#fff"/></svg>555-410-2287</div>
    <div class="row"><svg viewBox="0 0 12 12"><rect x="1" y="3" width="10" height="7" fill="#fff"/></svg>studio@harlowreeve.co</div>
    <div class="row"><svg viewBox="0 0 12 12"><circle cx="6" cy="6" r="5" fill="#fff"/></svg>www.harlowreeve.co</div>
  </div>

  <div class="foot-head" style="left:924px;top:100px;color:#fff">FOLLOW US ON</div>
  <div class="social"><span></span><span></span><span></span><span></span></div>
  <div class="rule" style="left:924px;top:170px;width:200px;background:#555"></div>
  <div class="call-label">CALL US ON</div>
  <div class="call-number">555-274-0913</div>
</footer>
<div class="foot-strip">&copy; 2015 All rights reserved by Harlow Reeve</div>

</body>
</html>
```